Home Remodeling company needs a business card design

we need a business card design for home remodeling company in hamilton county, indiana USA. we offers a wide range of construction services including whole house renovations, Design and Build Basements and Kitchen and Bathroom Remodeling . we would like to see designs for both site of business card that use the same color of the company logo and also including all information below :
1- Karim Feltous CEO / General Contractor
2- all company contacts Telephone numbers ( 1-888-DULOM-47 ) ( 317-555-0193) email address ( info@dulomhome.com) website ( www.dulomhome.com ) and social media logos (Facebook- twitter- google plus )
3- company logo
4- licensed . insured . bonded

```html
<!DOCTYPE html>
<html lang="en">
<head>
<meta charset="utf-8">
<title>Dulom Home Remodeling – Business Card</title>
<link href="https://fonts.googleapis.com/css2?family=Open+Sans:wght@400;600;700&display=swap" rel="stylesheet">
<style>
  :root {
    --backdrop: #3b3330;
    --card-black: #1c1c1d;
    --brand-red: #c8373f;
    --logo-grey: #4a4a4c;
    --text-white: #ffffff;
    --text-soft: #e9e9e9;
  }
  * { box-sizing: border-box; margin: 0; padding: 0; }
  html, body { width: 1200px; height: 844px; overflow: hidden; }
  body {
    background: var(--backdrop);
    font-family: "Open Sans", Arial, sans-serif;
    position: relative;
  }
  .card {
    position: absolute;
    top: 268px;
    width: 540px;
    height: 309px;
    border-radius: 3px;
    overflow: hidden;
    box-shadow: 0 14px 30px rgba(0,0,0,0.45);
  }
  /* Contact side */
  .card--contact { left: 40px; background: var(--card-black); }
  .contact-band {
    position: absolute; left: 0; right: 0; bottom: 0; height: 70px;
    background: var(--brand-red);
  }
  .social-row {
    position: absolute; left: 50%; top: 50%;
    transform: translate(-8%, -50%);
    display: flex; gap: 14px;
  }
  .social-dot {
    width: 30px; height: 30px; border-radius: 50%;
    background: var(--text-white);
  }
  .brand { position: absolute; left: 46px; top: 92px; }
  .brand-row { display: flex; align-items: center; gap: 10px; }
  .brand-mark { width: 10px; height: 10px; background: var(--brand-red); }
  .brand-name {
    font-weight: 700; font-size: 46px; line-height: 1;
    letter-spacing: 1px; color: var(--logo-grey);
  }
  .brand-sub {
    margin-top: 6px; margin-left: 20px;
    font-size: 13px; letter-spacing: 5.2px; color: var(--logo-grey);
  }
  .person {
    position: absolute; right: 30px; top: 40px;
    text-align: right;
  }
  .person-name { color: var(--brand-red); font-weight: 600; font-size: 15px; }
  .person-title { color: var(--text-soft); font-size: 12.5px; margin-top: 1px; }
  .contact-list { list-style: none; margin-top: 22px; }
  .contact-item {
    display: flex; justify-content: flex-end; align-items: center; gap: 7px;
    color: var(--text-soft); font-size: 12.5px; line-height: 21px;
  }
  .contact-icon { width: 11px; height: 11px; fill: var(--brand-red); }

  /* Brand side */
  .card--brand { left: 620px; background: var(--brand-red); }
  .brand--centered {
    left: 50%; top: 50%; transform: translate(-50%, -58%);
    text-align: left;
  }
  .brand--centered .brand-name { color: var(--text-white); font-size: 44px; }
  .brand--centered .brand-mark { background: var(--text-white); }
  .brand--centered .brand-sub { color: var(--text-white); }
  .tagline {
    margin-top: 8px; margin-left: 20px;
    color: var(--text-white); font-size: 14px; font-weight: 600;
  }
</style>
</head>
<body>

<section class="card card--contact" aria-label="Business card, contact side">
  <div class="brand">
    <div class="brand-row">
      <span class="brand-mark"></span>
      <span class="brand-name">DULOM</span>
    </div>
    <div class="brand-sub">HOME REMODELING</div>
  </div>

  <div class="person">
    <div class="person-name">Karim Feltous</div>
    <div class="person-title">CEO / General Contractor</div>
    <ul class="contact-list">
      <li class="contact-item">1-888-DULOM-47
        <svg class="contact-icon" viewBox="0 0 24 24"><path d="M6.6 10.8a15 15 0 0 0 6.6 6.6l2.2-2.2a1 1 0 0 1 1-.25 11.4 11.4 0 0 0 3.6.57 1 1 0 0 1 1 1V20a1 1 0 0 1-1 1A17 17 0 0 1 3 4a1 1 0 0 1 1-1h3.5a1 1 0 0 1 1 1c0 1.25.2 2.45.57 3.57a1 1 0 0 1-.25 1z"/></svg>
      </li>
      <li class="contact-item">317-555-0193
        <svg class="contact-icon" viewBox="0 0 24 24"><path d="M6.6 10.8a15 15 0 0 0 6.6 6.6l2.2-2.2a1 1 0 0 1 1-.25 11.4 11.4 0 0 0 3.6.57 1 1 0 0 1 1 1V20a1 1 0 0 1-1 1A17 17 0 0 1 3 4a1 1 0 0 1 1-1h3.5a1 1 0 0 1 1 1c0 1.25.2 2.45.57 3.57a1 1 0 0 1-.25 1z"/></svg>
      </li>
      <li class="contact-item">info@dulomhome.com
        <svg class="contact-icon" viewBox="0 0 24 24"><path d="M2 5h20v14H2z M2 5l10 8 10-8" /></svg>
      </li>
      <li class="contact-item">www.dulomhome.com
        <svg class="contact-icon" viewBox="0 0 24 24"><path d="M10 14l4-4M8 12l-3 3a3 3 0 0 0 4 4l3-3M16 12l3-3a3 3 0 0 0-4-4l-3 3" stroke="#c8373f" stroke-width="2.5" fill="none" stroke-linecap="round"/></svg>
      </li>
    </ul>
  </div>

  <div class="contact-band">
    <div class="social-row" aria-label="Social media links">
      <span class="social-dot"></span>
      <span class="social-dot"></span>
      <span class="social-dot"></span>
    </div>
  </div>
</section>

<section class="card card--brand" aria-label="Business card, brand side">
  <div class="brand brand--centered">
    <div class="brand-row">
      <span class="brand-mark"></span>
      <span class="brand-name">DULOM</span>
    </div>
    <div class="brand-sub">HOME REMODELING</div>
    <div class="tagline">Licensed • Insured • Bonded</div>
  </div>
</section>

</body>
</html>
```